New iOS App design for Boston Startup

We are looking for a new app design for our iPhone app. The current app's design feels outdated and we like to add lots of new functionality and a new navigation as well. A complete overhaul therefore!
We want you to design 5 screens that will have changed the most. The complete wireframes of these 5 pages are attached in the requirements document.
Once the winning design is selected we will award the winner with the designing all other screens (40-50 screens based on the same design). This will be a separate project worth $1000. The winning designer can get more follow up work if both sides are happy about the cooperation.
We will give feedback as soon as the first screen has been uploaded for review. Final decision will be made only after all 5 screens are finished.
We hope you give it your best!
Note: will only communicate through PixelHarbor (no skype),
Updates
Reason: Want to give designers a chance to submit their designs as I understand from some, the deadline is too close.
I have raised the award and introduced a 2nd price as well to make it worth your time. I hope you give it your best shot.
Reason: A few of you have asked for an extension of the deadline as time is running out. I will extend by one day. Tell me if you need more.
Industry/Entity Type
Startup
Requirements
Must have
- At least 1 screen before we can give you feedback.
Nice to have
- multiple options of 1 screen to get to a desirable design

```html
<!DOCTYPE html>
<html lang="en">
<head>
<meta charset="utf-8">
<title>Practice - SC</title>
<link rel="stylesheet" href="https://fonts.googleapis.com/css2?family=Roboto:wght@300;400;500;700&display=swap">
<style>
  :root {
    --status-bg: #000000;
    --header-red: #f05252;
    --header-edge: #b83434;
    --lesson-yellow: #fbc96b;
    --lesson-green: #7dd385;
    --lesson-blue: #3e9be4;
    --white: #ffffff;
    --page-bg: #ffffff;
    --tab-bg: #f7f7f7;
    --tab-line: #dcdcdc;
    --tab-icon: #666666;
    --tab-label: #555555;
  }
  * { margin: 0; padding: 0; box-sizing: border-box; }
  html, body { width: 676px; height: 1200px; overflow: hidden; background: var(--page-bg); }
  body { font-family: "Roboto", "Helvetica Neue", Arial, sans-serif; position: relative; }

  .status-bar {
    position: absolute; left: 0; top: 0; width: 676px; height: 42px;
    background: var(--status-bg); color: var(--white);
    font-weight: 700; font-size: 25px;
  }
  .status-bar .carrier { position: absolute; left: 48px; top: 6px; letter-spacing: 0.5px; }
  .status-bar .time { position: absolute; left: 0; width: 676px; top: 6px; text-align: center; }
  .status-bar svg { position: absolute; top: 0; }

  .app-header {
    position: absolute; left: 0; top: 42px; width: 676px; height: 93px;
    background: var(--header-red); border-bottom: 2px solid var(--header-edge);
  }
  .app-header .title {
    position: absolute; left: 0; width: 676px; top: 22px; text-align: center;
    color: var(--white); font-weight: 300; font-size: 41px;
  }
  .app-header .back { position: absolute; left: 27px; top: 29px; }

  .lesson-shapes { position: absolute; left: 0; top: 0; }
  .lesson {
    position: absolute; left: 0; width: 676px; height: 100px;
    color: var(--white); font-size: 26px; font-weight: 400;
  }
  .lesson .label { position: absolute; top: 33px; }
  .lesson .status-icon { position: absolute; top: 26px; }
  .lesson .chevron { position: absolute; top: 36px; }

  .tab-bar {
    position: absolute; left: 0; top: 1062px; width: 676px; height: 138px;
    background: var(--tab-bg); border-top: 3px solid var(--tab-line);
  }
  .tab {
    position: absolute; top: 19px; width: 108px; height: 107px;
    text-align: center; color: var(--tab-label); font-size: 21px;
  }
  .tab svg { display: block; margin: 12px auto 0; }
  .tab .tab-label { position: absolute; left: 0; width: 108px; top: 78px; }
  .tab.is-active { background: var(--header-red); color: var(--white); }
</style>
</head>
<body>

<header class="status-bar">
  <svg width="48" height="42" viewBox="0 0 48 42">
    <rect x="8" y="24" width="4" height="5" fill="#fff"/>
    <rect x="14" y="21" width="4" height="8" fill="#fff"/>
    <rect x="20" y="18" width="4" height="11" fill="#fff"/>
    <rect x="26" y="15" width="4" height="14" fill="#fff"/>
    <rect x="32" y="12" width="4" height="17" fill="#fff"/>
  </svg>
  <span class="carrier">ORBIT&nbsp;&nbsp;3G</span>
  <span class="time">9:51 PM</span>
  <svg style="left:590px" width="80" height="42" viewBox="0 0 80 42">
    <circle cx="10" cy="21" r="9" fill="#fff"/>
    <path d="M10 15 V21 H14" stroke="#000" stroke-width="2" fill="none"/>
    <rect x="36" y="11" width="34" height="20" rx="2" fill="none" stroke="#fff" stroke-width="2"/>
    <rect x="39" y="14" width="28" height="14" fill="#fff"/>
    <rect x="71" y="17" width="3" height="8" fill="#fff"/>
  </svg>
</header>

<div class="app-header">
  <svg class="back" width="42" height="42" viewBox="0 0 42 42">
    <circle cx="21" cy="21" r="20" fill="#fff"/>
    <path d="M10 21 L20 11 V17 H31 V25 H20 V31 Z" fill="var(--header-red)"/>
  </svg>
  <div class="title">Practice - SC</div>
</div>

<svg class="lesson-shapes" width="676" height="560" viewBox="0 0 676 560">
  <defs>
    <filter id="bubble-shadow" x="-5%" y="-20%" width="110%" height="150%">
      <feDropShadow dx="2" dy="4" stdDeviation="2.5" flood-color="#000" flood-opacity="0.45"/>
    </filter>
  </defs>
  <g stroke="#fff" stroke-width="4" filter="url(#bubble-shadow)">
    <path fill="var(--lesson-yellow)" d="M45,174 H633 Q657,174 657,198 V251 Q657,275 633,275 H48 Q25,276 6,287 Q20,268 21,245 V198 Q21,174 45,174 Z"/>
    <path fill="var(--lesson-green)" d="M40,301 H626 Q650,301 650,325 V370 Q652,392 672,412 Q646,404 624,401 H40 Q16,401 16,377 V325 Q16,301 40,301 Z"/>
    <path fill="var(--lesson-blue)" d="M45,428 H633 Q657,428 657,452 V505 Q657,529 633,529 H48 Q25,530 6,541 Q20,522 21,499 V452 Q21,428 45,428 Z"/>
  </g>
</svg>

<div class="lesson" style="top:174px">
  <span class="label" style="left:53px">Lesson 1: Sentence Correction</span>
  <svg class="status-icon" style="left:516px" width="44" height="48" viewBox="0 0 44 48">
    <path d="M2 22 H10 V46 H2 Z M13 22 L22 4 Q27 2 27 9 L25 18 H39 Q43 19 42 24 L38 42 Q37 46 32 46 H13 Z" fill="#fff"/>
  </svg>
  <svg class="chevron" style="left:620px" width="18" height="28" viewBox="0 0 18 28">
    <path d="M3 3 L14 14 L3 25" stroke="#fff" stroke-width="3" fill="none"/>
  </svg>
</div>

<div class="lesson" style="top:301px">
  <span class="label" style="left:49px">Lesson 2 : Sentence Correction</span>
  <svg class="status-icon" style="left:512px" width="44" height="48" viewBox="0 0 44 48">
    <path d="M2 22 H10 V46 H2 Z M13 22 L22 4 Q27 2 27 9 L25 18 H39 Q43 19 42 24 L38 42 Q37 46 32 46 H13 Z" fill="#fff"/>
  </svg>
  <svg class="chevron" style="left:618px" width="18" height="28" viewBox="0 0 18 28">
    <path d="M3 3 L14 14 L3 25" stroke="#fff" stroke-width="3" fill="none"/>
  </svg>
</div>

<div class="lesson" style="top:428px">
  <span class="label" style="left:53px">Lesson 3: Sentence Correction</span>
  <svg class="status-icon" style="left:514px" width="54" height="54" viewBox="0 0 54 54">
    <circle cx="27" cy="27" r="26" fill="#fff"/>
    <path d="M14 25 A13 13 0 0 1 37 18" stroke="var(--lesson-blue)" stroke-width="5" fill="none"/>
    <path d="M33 12 L42 14 L38 23 Z" fill="var(--lesson-blue)"/>
    <path d="M40 29 A13 13 0 0 1 17 36" stroke="var(--lesson-blue)" stroke-width="5" fill="none"/>
    <path d="M21 42 L12 40 L16 31 Z" fill="var(--lesson-blue)"/>
  </svg>
  <svg class="chevron" style="left:620px" width="18" height="28" viewBox="0 0 18 28">
    <path d="M3 3 L14 14 L3 25" stroke="#fff" stroke-width="3" fill="none"/>
  </svg>
</div>

<nav class="tab-bar">
  <div class="tab" style="left:25px">
    <svg width="70" height="52" viewBox="0 0 70 52">
      <g fill="var(--tab-icon)">
        <rect x="6" y="6" width="48" height="8"/>
        <rect x="12" y="17" width="54" height="8"/>
        <rect x="4" y="28" width="50" height="8"/>
        <rect x="10" y="39" width="52" height="9"/>
      </g>
    </svg>
    <span class="tab-label">Theory</span>
  </div>
  <div class="tab is-active" style="left:155px">
    <svg width="50" height="56" viewBox="0 0 50 56">
      <rect x="5" y="6" width="40" height="48" rx="3" fill="none" stroke="#fff" stroke-width="3"/>
      <rect x="16" y="1" width="18" height="9" rx="2" fill="#fff"/>
      <g fill="#fff">
        <rect x="20" y="18" width="20" height="3"/><rect x="20" y="25" width="20" height="3"/>
        <rect x="20" y="32" width="20" height="3"/><rect x="20" y="39" width="20" height="3"/>
        <rect x="20" y="46" width="20" height="3"/>
      </g>
    </svg>
    <span class="tab-label">Practice</span>
  </div>
  <div class="tab" style="left:287px">
    <svg width="56" height="52" viewBox="0 0 56 52">
      <path d="M28 3 L54 26 H47 V50 H34 V34 H22 V50 H9 V26 H2 Z" fill="var(--tab-icon)"/>
      <rect x="40" y="5" width="6" height="12" fill="var(--tab-icon)"/>
    </svg>
    <span class="tab-label">Home</span>
  </div>
  <div class="tab" style="left:421px">
    <svg width="58" height="52" viewBox="0 0 58 52">
      <path d="M14 12 H44 Q56 12 56 30 Q57 46 47 44 L39 34 H19 L11 44 Q1 46 2 30 Q2 12 14 12 Z" fill="var(--tab-icon)"/>
      <rect x="12" y="22" width="12" height="4" fill="#f7f7f7"/>
      <rect x="16" y="18" width="4" height="12" fill="#f7f7f7"/>
      <circle cx="40" cy="21" r="3" fill="#f7f7f7"/>
      <circle cx="46" cy="27" r="3" fill="#f7f7f7"/>
    </svg>
    <span class="tab-label">Games</span>
  </div>
  <div class="tab" style="left:553px">
    <svg width="54" height="58" viewBox="0 0 54 58">
      <rect x="5" y="6" width="40" height="48" fill="none" stroke="var(--tab-icon)" stroke-width="3"/>
      <g fill="var(--tab-icon)">
        <rect x="11" y="14" width="22" height="3"/><rect x="11" y="21" width="28" height="3"/>
        <rect x="11" y="28" width="28" height="3"/><rect x="11" y="35" width="28" height="3"/>
        <rect x="11" y="42" width="28" height="3"/>
      </g>
      <path d="M32 8 L38 15 L52 0" stroke="var(--tab-icon)" stroke-width="4" fill="none"/>
    </svg>
    <span class="tab-label">Test</span>
  </div>
</nav>

</body>
</html>
```